House flipping business web site needed

pinecrestholdingsgroup.example.
I am a residential developer in Northern NJ and I am looking for a fresh new updated website. I have an intro video about my company being made now. I don't update it very often but I want an easy format that I can add update photos to on projects I have worked on or homes I renovate for sale.

Target Market(s)

investors into my projects so a portfolio , people looking to sell their homes to me.

Industry/Entity Type

Real Estate Development

Number of Pages Required

4 page

Font styles to use
Serif

Colors
33b8a4
39a9d7
cadf82

Requirements
Must have
• space for an intro video about my company
• a portfolio with pictures and information about each project
• Markets we serve- Morris County, NJ
• My logo- already created
• SEO
• Yes I would like this to function over all platforms. Phone, computer, all platforms.
• history and background page
• I am looking for a completed page that I can upload to the site that hosts my website
Nice to have
• I want something creative, easy to navigate. modern.

```html
<!DOCTYPE html>
<html lang="en">
<head>
<meta charset="utf-8">
<title>Pinecrest Holdings Group</title>
<link href="https://fonts.googleapis.com/css2?family=Raleway:wght@400;600;700&family=Open+Sans:ital,wght@0,400;0,600;0,700;1,400&display=swap" rel="stylesheet">
<style>
:root{
  --teal:#33b8a4;
  --blue:#39a9d7;
  --lime:#cadf82;
  --ink:#222;
  --text:#666;
  --light:#f5f5f5;
  --footer:#1b1b1b;
  --white:#fff;
}
*{margin:0;padding:0;box-sizing:border-box}
html,body{width:794px;height:1200px;overflow:hidden}
body{position:relative;font-family:"Open Sans",sans-serif;color:var(--text);background:var(--white)}
.abs{position:absolute}
.heading{font-family:"Raleway",sans-serif;font-weight:700;color:var(--ink);text-transform:uppercase}
.accent{position:absolute;width:12px;height:2px;background:var(--lime)}

/* hero */
.hero{left:0;top:0;width:794px;height:338px;background:linear-gradient(180deg,#6f6f6f 0%,#8a8378 45%,#5b5148 80%,#3f3a33 100%)}
.nav-bar{left:162px;top:0;width:471px;height:32px;background:rgba(255,255,255,.96)}
.nav{position:absolute;left:216px;top:0;display:flex;gap:0;height:32px}
.nav a{font-family:"Raleway",sans-serif;font-size:5.5px;font-weight:600;color:#333;text-decoration:none;line-height:32px;padding:0 7px;position:relative}
.nav a.active{color:var(--teal)}
.nav a.active::after{content:"";position:absolute;left:0;right:0;bottom:0;height:2px;background:var(--teal)}
.search{position:absolute;left:444px;top:9px;width:14px;height:14px;border-radius:50%;background:var(--blue)}
.logo{left:170px;top:0;width:84px;height:72px;background:var(--white);box-shadow:0 1px 3px rgba(0,0,0,.15);display:flex;flex-direction:column;align-items:center;justify-content:center;gap:4px}
.logo-mark{width:18px;height:18px;border-radius:50%;background:var(--blue)}
.logo-name{font-family:"Raleway",sans-serif;font-weight:700;font-size:7px;color:var(--blue);text-align:center;line-height:1.2;letter-spacing:.3px}
.hero-title{left:156px;top:252px;font-family:"Raleway",sans-serif;font-weight:700;font-size:8px;color:var(--white);text-transform:uppercase}
.hero-btn{left:155px;top:275px;width:71px;height:18px;border:1.5px solid var(--teal);border-radius:10px;font-family:"Raleway",sans-serif;font-weight:700;font-size:4.5px;color:var(--white);text-align:center;line-height:15px}
.dots{left:754px;top:161px;display:flex;flex-direction:column;gap:3px}
.dots span{width:4px;height:4px;border-radius:50%;background:var(--white)}
.dots span:first-child{background:var(--teal)}

/* about */
.about-h{left:162px;top:385px;font-size:10px}
.about-lead{left:162px;top:403px;width:230px;font-size:5.6px;color:#222;line-height:1.8}
.about-body{left:162px;top:432px;width:230px;font-size:4.6px;line-height:1.75}
.more{font-family:"Raleway",sans-serif;font-weight:700;font-size:4.8px;color:var(--teal);text-transform:uppercase}
.video{left:405px;top:358px;width:233px;height:131px;border:2px solid #e6e6e6;background:linear-gradient(180deg,#7c7d78 0%,#9a9a91 45%,#58624a 75%,#4a5a2f 100%)}
.play{position:absolute;left:107px;top:56px;width:18px;height:18px;border-radius:50%;background:var(--white)}

/* portfolio */
.portfolio{left:0;top:506px;width:794px;height:274px;background:var(--light)}
.sec-title{left:0;width:794px;text-align:center;font-size:9.5px}
.sec-sub{left:0;width:794px;text-align:center;font-size:4.8px;color:#888}
.card{top:582px;width:109px;height:166px;background:var(--white);box-shadow:0 1px 2px rgba(0,0,0,.08)}
.card-img{position:absolute;left:0;top:0;width:109px;height:89px}
.card-btn{position:absolute;right:0;top:79px;height:10px;display:flex}
.card-btn b{font-family:"Raleway",sans-serif;font-size:4px;color:var(--white);background:var(--blue);padding:0 6px;line-height:10px}
.card-btn i{width:6px;background:#1a7fae}
.card.lime .card-btn b{background:var(--lime)}
.card.lime .card-btn i{background:#a8bd5e}
.card .accent{left:12px;top:102px}
.card h3{position:absolute;left:12px;top:106px;font-size:7px}
.card p{position:absolute;left:12px;top:121px;width:88px;font-size:4.6px;line-height:1.75}
.arrow{top:652px}

/* news */
.news-h{left:162px;top:812px;font-size:10px}
.news-item{top:835px;width:140px}
.news-item .date{position:absolute;left:23px;top:0;font-size:4.2px;color:#999}
.news-item h4{position:absolute;left:23px;top:7px;width:125px;font-family:"Raleway",sans-serif;font-size:7.2px;font-weight:600;color:#222;line-height:1.4}
.news-item p{position:absolute;left:23px;top:40px;width:125px;font-size:4.6px;line-height:1.75}
.news-item .more{position:absolute;top:88px;color:var(--blue)}
.quote{left:484px;top:835px;width:149px;height:107px;background:var(--light)}
.quote p{position:absolute;left:20px;top:19px;width:110px;text-align:center;font-style:italic;font-size:4.6px;line-height:1.8;color:#888}
.quote .who{position:absolute;left:0;width:149px;top:74px;text-align:center;font-family:"Raleway",sans-serif;font-weight:700;font-size:4.8px;color:#333}
.quote .role{position:absolute;left:0;width:149px;top:83px;text-align:center;font-family:"Raleway",sans-serif;font-weight:700;font-size:4.3px;color:#999}
.qbtn{position:absolute;top:45px;width:15px;height:15px}

/* markets */
.markets{left:0;top:976px;width:794px;height:56px;background:var(--blue);display:flex;justify-content:center;align-items:center;gap:14px;font-family:"Raleway",sans-serif;color:var(--white)}
.markets .lbl{font-size:14px}
.markets .area{font-size:15.5px;font-weight:600}

/* footer */
.footer{left:0;top:1032px;width:794px;height:168px;background:var(--footer)}
.f-h{top:1059px;font-family:"Raleway",sans-serif;font-weight:700;font-size:6px;color:var(--white);text-transform:uppercase}
.f-txt{font-size:4.8px;color:#bbb;line-height:1.75}
.f-list{list-style:none;font-size:4.8px;color:#bbb}
.f-list li{height:10.3px}
.f-list li::before{content:"›";margin-right:4px}
.sub-field{left:155px;top:1117px;width:108px;height:16px;border:1px solid #444;font-style:italic;font-size:4.8px;color:#888;line-height:14px;padding-left:7px}
.sub-btn{left:248px;top:1117px;width:15px;height:16px;background:var(--teal)}
.f-rule{left:155px;top:1175px;width:484px;height:1px;background:#333}
.copy{left:155px;top:1184px;font-size:4.2px;color:#aaa}
.social{top:1180px;width:12px;height:12px;border:1px solid #444}
</style>
</head>
<body>

<!-- hero -->
<div class="abs hero" role="img" aria-label="Photo of a renovated two-storey house with stone landscaping and bare trees"></div>
<div class="abs nav-bar">
  <nav class="nav">
    <a class="active">HOME</a><a>SERVICES</a><a>PORTFOLIO</a><a>ABOUT US</a><a>NEWS</a><a>CONTACT</a>
  </nav>
  <svg class="search" viewBox="0 0 14 14"><circle cx="6.3" cy="6.3" r="2.3" fill="none" stroke="#fff" stroke-width="1"/><line x1="8" y1="8" x2="9.8" y2="9.8" stroke="#fff" stroke-width="1"/></svg>
</div>
<div class="abs logo">
  <div class="logo-mark"></div>
  <div class="logo-name">PINECREST<br>HOLDINGS GROUP</div>
</div>
<div class="abs hero-title">We bring excellence to the home buying and renovation business.</div>
<div class="abs hero-btn">VIEW DETAILS</div>
<div class="abs dots"><span></span><span></span><span></span><span></span></div>

<!-- about -->
<div class="accent" style="left:162px;top:381px"></div>
<h2 class="abs heading about-h">About Us</h2>
<p class="abs about-lead">We only buy and renovate homes in our neighborhoods right here in the Morris County, NJ area.</p>
<p class="abs about-body">Is a house in your neighborhood an eyesore? Is it vacant, boarded up and a hazard to the neighborhood? Please contact us and we can help transform that property into a beautiful home</p>
<div class="abs more" style="left:161px;top:463px">Read more ›</div>
<div class="abs video" role="img" aria-label="Company intro video still of a lakeside house behind a stone wall">
  <svg class="play" viewBox="0 0 18 18"><circle cx="9" cy="9" r="9" fill="#fff"/><circle cx="9" cy="9" r="7.5" fill="#222"/><path d="M7 5.5 L12.5 9 L7 12.5Z" fill="#fff"/></svg>
</div>

<!-- portfolio -->
<div class="abs portfolio"></div>
<h2 class="abs heading sec-title" style="top:535px">Our Portfolio</h2>
<p class="abs sec-sub" style="top:549px">Donec ornare pellentesque tellus sed porttitor</p>
<div class="accent" style="left:391px;top:560px"></div>

<svg class="abs arrow" style="left:124px" width="14" height="28" viewBox="0 0 14 28"><path d="M13 1 L1 14 L13 27" fill="none" stroke="#bbb" stroke-width="1"/></svg>
<svg class="abs arrow" style="left:657px" width="14" height="28" viewBox="0 0 14 28"><path d="M1 1 L13 14 L1 27" fill="none" stroke="#bbb" stroke-width="1"/></svg>

<article class="abs card" style="left:162px">
  <div class="card-img" role="img" aria-label="Renovated colonial house in Rockaway" style="background:linear-gradient(180deg,#9fb0c2 0%,#7e8a6d 55%,#4f6a35 100%)"></div>
  <div class="card-btn"><b>READ MORE</b><i></i></div>
  <div class="accent"></div>
  <h3 class="heading">Rockaway, NJ</h3>
  <p>Lorem ipsum dolor sit amet, consectetur adipiscing elit. Mauris faucibus sapien ut elit condimentum congue.</p>
</article>
<article class="abs card lime" style="left:282px">
  <div class="card-img" role="img" aria-label="Small house under renovation in Denville" style="background:linear-gradient(180deg,#6c7d5a 0%,#8e8e8a 50%,#6a5a4c 100%)"></div>
  <div class="card-btn"><b>READ MORE</b><i></i></div>
  <div class="accent"></div>
  <h3 class="heading">Denville, NJ</h3>
  <p>Lorem ipsum dolor sit amet, consectetur adipiscing elit. Mauris faucibus sapien ut elit condimentum congue.</p>
</article>
<article class="abs card" style="left:403px">
  <div class="card-img" role="img" aria-label="Blue cottage among trees in Boonton" style="background:linear-gradient(180deg,#6f8c4e 0%,#7fa0a4 55%,#5c7a3e 100%)"></div>
  <div class="card-btn"><b>READ MORE</b><i></i></div>
  <div class="accent"></div>
  <h3 class="heading">Boonton, NJ</h3>
  <p>Lorem ipsum dolor sit amet, consectetur adipiscing elit. Mauris faucibus sapien ut elit condimentum congue.</p>
</article>
<article class="abs card" style="left:524px">
  <div class="card-img" role="img" aria-label="Warehouse construction site with excavator" style="background:linear-gradient(180deg,#6fa0d8 0%,#b89c7e 55%,#6b5a44 100%)"></div>
  <div class="card-btn"><b>READ MORE</b><i></i></div>
  <div class="accent"></div>
  <h3 class="heading">Warehousing</h3>
  <p>Lorem ipsum dolor sit amet, consectetur adipiscing elit. Mauris faucibus sapien ut elit condimentum congue.</p>
</article>

<!-- news -->
<div class="accent" style="left:162px;top:808px"></div>
<h2 class="abs heading news-h">Latest News</h2>
<article class="abs news-item" style="left:162px">
  <svg style="position:absolute;left:0;top:0" width="14" height="14" viewBox="0 0 14 14"><rect x="1" y="2" width="12" height="11" fill="none" stroke="var(--teal)" stroke-width="1"/><rect x="1" y="2" width="12" height="3" fill="var(--teal)"/><path d="M3 7h8M3 9h8M3 11h8M5 5v8M7 5v8M9 5v8" stroke="var(--teal)" stroke-width=".5"/></svg>
  <div class="date">APRIL 22, 2016</div>
  <h4>Vestibulum ante ipsum primis in faucibus orci luctus</h4>
  <p>Donec ornare pellentesque tellus sed porttitor. Sed porta nec leo et scelerisque. Nullam at est interdum, hendrerit nibh in, efficitur neque. Proin lobortis metus vel nisl faucibus, id eleifend lorem laoreet.</p>
  <div class="more" style="left:111px">Read more ›</div>
</article>
<article class="abs news-item" style="left:322px">
  <svg style="position:absolute;left:0;top:0" width="14" height="14" viewBox="0 0 14 14"><rect x="1" y="2" width="12" height="11" fill="none" stroke="var(--teal)" stroke-width="1"/><rect x="1" y="2" width="12" height="3" fill="var(--teal)"/><path d="M3 7h8M3 9h8M3 11h8M5 5v8M7 5v8M9 5v8" stroke="var(--teal)" stroke-width=".5"/></svg>
  <div class="date">APRIL 22, 2016</div>
  <h4>Vestibulum ante ipsum primis in faucibus orci luctus</h4>
  <p>Tellus sed porttitor. Sed porta nec leo et scelerisque. Nullam at est interdum, hendrerit nibh in, efficitur neque. Proin lobortis metus vel nisl faucibus, id eleifend lorem laoreet. Maecenas sit amet lorem eu purus rutrum interdum.</p>
  <div class="more" style="left:112px">Read more ›</div>
</article>

<div class="accent" style="left:484px;top:808px"></div>
<h2 class="abs heading news-h" style="left:484px">What Clients Say</h2>
<div class="abs quote">
  <p>Nam et libero nec ex tincidunt malesuada vel sit amet arcu. Sed sit amet est nec quam hendrerit hendrerit. Curabitur ut pulvinar mi.</p>
  <svg class="qbtn" style="left:0" viewBox="0 0 15 15"><rect width="15" height="15" fill="#1e2b33"/><path d="M8.5 4.5 L5.5 7.5 L8.5 10.5" fill="none" stroke="#fff" stroke-width="1.2"/></svg>
  <svg class="qbtn" style="left:133px" viewBox="0 0 15 15"><rect width="15" height="15" fill="var(--blue)"/><path d="M6.5 4.5 L9.5 7.5 L6.5 10.5" fill="none" stroke="#fff" stroke-width="1.2"/></svg>
  <div class="who">JHON DOE</div>
  <div class="role">TLOREM ISPUM DOLOR SIT</div>
</div>

<!-- markets -->
<div class="abs markets"><span class="lbl">Markets we serve -</span><span class="area">MORRIS COUNTY, NJ</span></div>

<!-- footer -->
<div class="abs footer"></div>
<h3 class="abs f-h" style="left:155px">Newsletter Subscribe</h3>
<p class="abs f-txt" style="left:155px;top:1077px;width:104px">Subscribe to our newsletter and we will inform you about newset projects and promotions.</p>
<div class="abs sub-field">Your email address</div>
<svg class="abs sub-btn" viewBox="0 0 15 16"><rect width="15" height="16" fill="var(--teal)"/><rect x="4.5" y="6" width="6" height="4.5" fill="#fff"/><path d="M4.5 6 L7.5 8.5 L10.5 6" fill="none" stroke="var(--teal)" stroke-width=".6"/></svg>

<h3 class="abs f-h" style="left:324px">Quick Links</h3>
<ul class="abs f-list" style="left:324px;top:1078px">
  <li>Home</li><li>About</li><li>Services</li><li>Gallery</li><li>Testimonials</li><li>Portfolio</li><li>Contact</li>
</ul>

<h3 class="abs f-h" style="left:437px">More Links</h3>
<ul class="abs f-list" style="left:437px;top:1078px">
  <li>Privacy Policy</li><li>Terms &amp; Conditions</li><li>FAQ</li><li>Lorem</li><li>Ipsum dolor</li><li>Dolor sit amit</li><li>More</li>
</ul>

<h3 class="abs f-h" style="left:558px">Contact Us</h3>
<p class="abs f-txt" style="left:558px;top:1077px;width:90px">48 Birchwood Ln. Cedar Falls, NJ<br>07999</p>
<p class="abs" style="left:558px;top:1099px;font-size:7px;color:#fff">Phone: 555.013.2847</p>
<p class="abs f-txt" style="left:558px;top:1113px">Fax: 555.013.9160<br>hello@pinecrestholdingsgroup.example</p>

<div class="abs f-rule"></div>
<p class="abs copy">COPYRIGHTS 2016 © YOURSITE. ALL RIGHTS RESERVED</p>
<div class="abs social" style="left:598px"></div>
<div class="abs social" style="left:613px"></div>
<div class="abs social" style="left:628px"></div>

</body>
</html>
```